Brightlane Rapid Rinse Web Design

We are looking for a web design that highlights our state of the art fully automated commercial vehicle washing equipment. Similar system to a car wash however this system is meant for the largest vehicles on our roadways. Transport trucks with or without a trailer, busses both highway and school, RV's from 5th wheel type to A Class. Cement trucks, dump trucks, vac trucks, fuel trucks etc. Pick ups with utility trailers...Refrigerator truck clean outs.
Brightlane Rapid Rinse will wash your vehicle quickly and with a minimal impact on the environment

Home page
About us
Why Brightlane
Services and pricing
Videos of wash system
Fleets
contact us

Target Market(s)

Commercial vehicle owners and operators as well as corporate fleets. Includes busses, municipal, school and highway.both school and

Industry/Entity Type

transportation

Coding

Coded - Design and coding required

Number of Pages Required

5+ page

Font styles to use
Sans Serif

Colors
0054AA
0677BA
7BADD7
CADEEF
E8F1F8

Requirements
Must have
• Welcome page,why us page which describes the financial and environmental benefits. payment processing page, contact us page, Services which is washing vehicles and greasing for commercial vehicles that want that service and grease
Nice to have
• pictures of both clean and dirty commercial vehicles ie. before and after

```html
<!DOCTYPE html>
<html lang="en">
<head>
<meta charset="utf-8">
<title>Brightlane Rapid Rinse</title>
<link href="https://fonts.googleapis.com/css2?family=Lato:wght@300;400;700;900&display=swap" rel="stylesheet">
<style>
:root{
  --brand:#0677BA;
  --brand-deep:#0054AA;
  --brand-mid:#7BADD7;
  --brand-soft:#CADEEF;
  --brand-pale:#E8F1F8;
  --ink:#111;
  --body:#4a4a4a;
  --night:#0b1628;
  --white:#fff;
}
*{box-sizing:border-box;margin:0;padding:0}
html,body{width:1200px;height:4179px;overflow:hidden}
body{font-family:'Lato',sans-serif;color:var(--ink);background:var(--white);position:relative}
a{color:inherit;text-decoration:none}
.abs{position:absolute}
.btn{position:absolute;display:flex;align-items:center;justify-content:center;font-size:15px;border-radius:2px}
.btn-blue{background:var(--brand);color:var(--white)}
.btn-white{background:var(--white);color:var(--brand)}
.photo{position:absolute}
.section-title{position:absolute;left:0;width:1200px;text-align:center;font-size:45px;font-weight:700;color:var(--ink)}

/* header */
.site-header{position:absolute;top:0;left:0;width:1200px;height:130px;background:var(--white)}
.logo{position:absolute;left:106px;top:14px;font-size:40px;font-weight:700;line-height:48px;text-align:center;color:var(--ink)}
.contact-item{position:absolute;top:37px;display:flex;align-items:center;gap:14px}
.contact-icon{width:52px;height:52px;border-radius:50%;background:var(--brand);display:flex;align-items:center;justify-content:center}
.contact-label{font-size:14px;color:#777;line-height:22px}
.contact-value{font-size:15px;color:var(--ink);line-height:22px}

/* hero */
.hero{position:absolute;top:130px;left:0;width:1200px;height:640px}
.hero-photo{left:0;top:0;width:1200px;height:640px;background:linear-gradient(100deg,#1f2d3b 0%,#3b4f60 35%,#5d7a8e 60%,#2d3a45 100%)}
.main-nav{position:absolute;top:0;left:0;width:1200px;height:68px;background:rgba(6,119,186,.85);display:flex;justify-content:center;align-items:center;gap:41px;padding-right:22px;font-size:15px;color:var(--white)}
.hero-kicker{position:absolute;left:113px;top:170px;font-size:42px;font-weight:400;color:var(--white)}
.hero-title{position:absolute;left:107px;top:240px;font-size:84px;line-height:96px;font-weight:700;color:var(--white)}
.hero-person{left:662px;top:332px;width:270px;height:329px;border-radius:130px 130px 0 0;background:linear-gradient(180deg,#2f6cc4 0%,#1d4f9c 60%,#173f82 100%)}
.hero-badge{position:absolute;left:868px;top:389px;width:300px;height:130px;background:var(--brand);border-radius:8px;color:var(--white);font-size:31px;font-weight:700;line-height:46px;text-align:center;padding-top:18px}

/* services */
.service-card{position:absolute;top:952px;width:314px;height:386px;background:var(--white);box-shadow:0 2px 8px rgba(0,0,0,.18);border-radius:4px;text-align:center}
.service-card .photo{left:0;top:0;width:314px;height:204px;border-radius:4px 4px 0 0}
.service-card h3{position:absolute;top:224px;left:0;width:100%;font-size:23px;font-weight:700;color:var(--brand)}
.service-card p{position:absolute;top:262px;left:38px;width:238px;font-size:15px;line-height:21px;color:var(--body)}
.arrow-dot{position:absolute;left:136px;bottom:-21px;width:42px;height:42px;border-radius:50%;background:var(--brand);display:flex;align-items:center;justify-content:center}

/* about */
.about-title{position:absolute;left:115px;top:1436px;font-size:45px;font-weight:700}
.about-text{position:absolute;left:112px;top:1520px;width:445px;font-size:15px;line-height:26px;color:var(--body)}
.about-text p+p{margin-top:26px}
.dots{position:absolute;background-image:radial-gradient(#9aa3ad 1px,transparent 1.3px);background-size:6px 6px}

/* gallery */
.gallery{position:absolute;top:1943px;left:0;width:1200px;height:687px;background:var(--brand-pale)}
.gallery .photo{border-radius:2px}

/* mission */
.mission{position:absolute;top:2630px;left:0;width:1200px;height:438px;background:linear-gradient(90deg,#0866b0,#0677BA 50%,#0a6fb6)}
.mission-title{position:absolute;left:0;top:65px;width:1200px;text-align:center;font-size:45px;font-weight:700;color:var(--white)}
.mission-text{position:absolute;left:180px;top:147px;width:840px;text-align:center;font-size:14.5px;line-height:26px;color:var(--white)}

/* pricing */
.pricing{position:absolute;left:114px;top:3240px;width:973px;height:307px;display:flex}
.pricing > div{width:243.25px;height:307px;position:relative}
.price-panel{background:var(--brand);color:var(--white)}
.price-panel h3{position:absolute;left:24px;top:28px;font-size:23px;font-weight:700}
.price-panel p{position:absolute;left:27px;top:92px;width:195px;font-size:14.5px;line-height:22px}
.price-panel .btn{left:27px;top:232px;width:138px;height:42px}

/* footer */
.site-footer{position:absolute;top:3634px;left:0;width:1200px;height:486px;background:var(--night);color:var(--white)}
.footer-logo{position:absolute;left:108px;top:44px;font-size:40px;font-weight:700;line-height:48px;text-align:center}
.footer-divider-v{position:absolute;left:413px;top:62px;width:1px;height:60px;background:#4b5566}
.news{position:absolute;left:449px;top:62px}
.news h4{font-size:25px;font-weight:700}
.news p{font-size:12px;line-height:18px;margin-top:6px;color:#d8dde5}
.email-field{position:absolute;left:715px;top:66px;width:238px;height:46px;border:1px solid #cfd6df;border-radius:3px;font-size:13px;padding:14px 18px;display:flex;justify-content:space-between}
.subscribe{position:absolute;left:966px;top:66px;width:122px;height:46px;background:var(--brand);border-radius:3px;display:flex;align-items:center;justify-content:center;font-size:15px}
.footer-rule{position:absolute;left:112px;top:190px;width:976px;height:1px;background:#2d3a4e}
.footer-col h5{position:absolute;font-size:19px;font-weight:700;top:245px}
.footer-list{position:absolute;top:292px;list-style:none;font-size:15px}
.footer-list li{height:36px;display:flex;align-items:flex-start;gap:16px}
.footer-list li::before{content:"›";color:var(--brand-mid);font-size:17px;line-height:16px}
.footer-about{position:absolute;left:112px;top:292px;width:240px;font-size:14.5px;line-height:22px}
.socials{position:absolute;left:112px;top:384px;display:flex;gap:17px}
.socials span{width:17px;height:17px;border-radius:50%;border:2px solid var(--white)}
.copyright{position:absolute;top:4120px;left:0;width:1200px;height:59px;background:var(--brand);color:var(--white);font-size:13px;display:flex;align-items:center;justify-content:center}
</style>
</head>
<body>

<header class="site-header">
  <div class="logo">Brightlane<br>Rapid Rinse</div>
  <div class="contact-item" style="left:485px">
    <div class="contact-icon"><svg width="24" height="24" viewBox="0 0 24 24"><path fill="#fff" d="M6.6 10.8a15.1 15.1 0 0 0 6.6 6.6l2.2-2.2c.3-.3.7-.4 1-.2 1.1.4 2.3.6 3.6.6.6 0 1 .4 1 1V20c0 .6-.4 1-1 1A17 17 0 0 1 3 4c0-.6.4-1 1-1h3.5c.6 0 1 .4 1 1 0 1.3.2 2.5.6 3.6.1.3 0 .7-.2 1z"/></svg></div>
    <div><div class="contact-label">Call Us</div><div class="contact-value">+1 555 010 2040</div></div>
  </div>
  <div class="contact-item" style="left:713px">
    <div class="contact-icon"><svg width="24" height="24" viewBox="0 0 24 24"><circle cx="12" cy="12" r="8.5" fill="none" stroke="#fff" stroke-width="2.4"/><path d="M12 7v5.5l3 2" fill="none" stroke="#fff" stroke-width="2.4" stroke-linecap="round"/></svg></div>
    <div><div class="contact-label">Opening Time</div><div class="contact-value">9:00am - 6:00pm</div></div>
  </div>
  <a class="btn btn-blue" style="left:951px;top:44px;width:136px;height:41px">Contact Us</a>
</header>

<section class="hero">
  <div class="photo hero-photo" role="img" aria-label="Commercial truck being pressure washed inside the wash bay"></div>
  <nav class="main-nav">
    <a>Home</a><a>About us</a><a>Why Brightlane</a><a>Services and pricing</a><a>Videos of wash system</a><a>Fleets</a><a>Contact us</a>
  </nav>
  <div class="hero-kicker">Welcome to</div>
  <h1 class="hero-title">Brightlane<br>Rapid Rinse</h1>
  <a class="btn btn-blue" style="left:110px;top:478px;width:138px;height:41px">Book a Wash</a>
  <a class="btn btn-white" style="left:264px;top:478px;width:138px;height:41px">Learn More</a>
</section>

<svg class="abs" style="left:0;top:700px" width="1200" height="100" viewBox="0 0 1200 100">
  <path d="M0 70 H470 C520 70 540 40 592 38 C640 36 660 70 720 70 H1200 V100 H0Z" fill="#fff"/>
  <circle cx="592" cy="60" r="13" fill="#0677BA"/>
  <path d="M592 53v13M586 61l6 6 6-6" stroke="#fff" stroke-width="2.4" fill="none" stroke-linecap="round"/>
</svg>
<div class="photo hero-person" role="img" aria-label="Wash technician in blue coveralls and hard hat pointing to the wash time"></div>
<div class="hero-badge">Less<br>Than 15 Minutes</div>

<h2 class="section-title" style="top:862px">Services</h2>

<article class="service-card" style="left:111px">
  <div class="photo" role="img" aria-label="Automated wash brushes inside the truck bay" style="background:linear-gradient(180deg,#3c4a4f,#2f6f70 50%,#222 100%)"></div>
  <h3>Automated Truck Wash</h3>
  <p>Excepteur sint occaecat cupidatat proident, sunt in culpa qui officia deserunt mollit anim id est laborum.</p>
  <div class="arrow-dot"><svg width="16" height="16" viewBox="0 0 16 16"><path d="M2 8h11M8 3l5 5-5 5" stroke="#fff" stroke-width="2.6" fill="none"/></svg></div>
</article>
<article class="service-card" style="left:443px">
  <div class="photo" role="img" aria-label="Worker rinsing a truck grille with a pressure washer" style="background:linear-gradient(120deg,#7a6a5a,#a9afb6 50%,#5f6870)"></div>
  <h3>Additional Services</h3>
  <p>Excepteur sint occaecat cupidatat proident, sunt in culpa qui officia deserunt mollit anim id est laborum.</p>
  <div class="arrow-dot"><svg width="16" height="16" viewBox="0 0 16 16"><path d="M2 8h11M8 3l5 5-5 5" stroke="#fff" stroke-width="2.6" fill="none"/></svg></div>
</article>
<article class="service-card" style="left:774px">
  <div class="photo" role="img" aria-label="Fleet truck parked in a service garage" style="background:linear-gradient(180deg,#3a4450,#9aa2aa 55%,#6a5a50)"></div>
  <h3>Fleet Services</h3>
  <p>Excepteur sint occaecat cupidatat proident, sunt in culpa qui officia deserunt mollit anim id est laborum.</p>
  <div class="arrow-dot"><svg width="16" height="16" viewBox="0 0 16 16"><path d="M2 8h11M8 3l5 5-5 5" stroke="#fff" stroke-width="2.6" fill="none"/></svg></div>
</article>

<h2 class="about-title">About Us</h2>
<div class="about-text">
  <p>Lorem ipsum dolor sit amet, consectetur adipiscing elit, sed do eiusmod tempor incididunt ut labore et dolore magna aliqua. Ut enim ad minim veniam, quis nostrud exercitation ullamco laboris nisi ut aliquip ex ea commodo consequat.</p>
  <p>Duis aute irure dolor in reprehenderit in voluptate velit esse cillum dolore eu fugiat nulla pariatur. Excepteur sint occaecat cu pidatat non proident, sunt in culpa qui officia deserunt mollit anim id est laborum.</p>
</div>
<a class="btn btn-blue" style="left:112px;top:1808px;width:136px;height:41px">Read More</a>
<div class="dots" style="left:932px;top:1478px;width:120px;height:78px"></div>
<div class="dots" style="left:652px;top:1742px;width:120px;height:78px"></div>
<div class="photo" role="img" aria-label="Wash bay brushes scrubbing a trailer" style="left:772px;top:1553px;width:315px;height:299px;background:linear-gradient(135deg,#1d2f55,#3e5f98 50%,#172645)"></div>
<div class="photo" role="img" aria-label="Close-up of a truck headlight being sprayed" style="left:618px;top:1446px;width:314px;height:297px;border-radius:6px 0 0 6px;background:linear-gradient(135deg,#2a2f36,#5c646c 50%,#1d2126)"></div>

<section class="gallery">
  <h2 class="section-title" style="top:92px">Gallery</h2>
  <div class="photo" role="img" aria-label="Tanker truck on the highway at sunset" style="left:114px;top:188px;width:225px;height:160px;background:linear-gradient(180deg,#d89a6a,#5a6f8a 60%,#4a4a4a)"></div>
  <div class="photo" role="img" aria-label="White cement mixer truck" style="left:114px;top:376px;width:225px;height:160px;background:linear-gradient(180deg,#a9c6e0,#dfe4e8 60%,#6d6d6d)"></div>
  <div class="photo" role="img" aria-label="Before and after comparison of a dirty and a clean trailer" style="left:362px;top:188px;width:476px;height:348px;background:linear-gradient(90deg,#7c6a55 0%,#9a7554 45%,#e4e8ec 55%,#c6ccd2 100%)"></div>
  <svg class="abs" style="left:362px;top:188px" width="476" height="348">
    <line x1="270" y1="0" x2="270" y2="348" stroke="#222" stroke-width="2"/>
    <circle cx="270" cy="174" r="20" fill="#fff" stroke="#555"/>
    <path d="M264 169l-5 5 5 5M276 169l5 5-5 5" stroke="#333" stroke-width="1.6" fill="none"/>
  </svg>
  <div class="photo" role="img" aria-label="Vacuum truck under a grey sky" style="left:864px;top:188px;width:224px;height:160px;background:linear-gradient(180deg,#8fa2b4,#c7ccd1 60%,#6a6e72)"></div>
  <div class="photo" role="img" aria-label="Blue dump truck" style="left:864px;top:376px;width:224px;height:160px;background:linear-gradient(180deg,#a8b6c4,#2d4f9a 60%,#555)"></div>
  <a class="btn btn-blue" style="left:532px;top:564px;width:138px;height:42px">View All</a>
</section>

<section class="mission">
  <div class="photo" role="img" aria-label="Faded image of a worker washing a truck" style="left:0;top:0;width:440px;height:438px;background:linear-gradient(90deg,rgba(0,40,90,.35),rgba(6,119,186,0))"></div>
  <h2 class="mission-title">Our Mission</h2>
  <p class="mission-text">Sed ut perspiciatis unde omnis iste natus error sit voluptatem accusantium doloremque laudantium, totam rem aperiam, eaque ipsa quae ab illo inventore veritatis et quasi architecto beatae vitae dicta sunt explicabo. Nemo enim ipsam voluptatem quia voluptas sit aspernatur aut odit aut fugit, sed quia consequuntur magni dolores eos qui ratione voluptatem sequi nesci-unt. Neque porro quisquam est, qui dolorem ipsum quia dolor sit amet, consectetur, adipisci velit, sed quia non numquam eius modi tempora incidunt ut labore et dolore magnam aliquam quaerat voluptatem.</p>
  <a class="btn btn-white" style="left:532px;top:299px;width:138px;height:42px">Read More</a>
  <svg class="abs" style="left:0;top:378px" width="1200" height="60" viewBox="0 0 1200 60">
    <path d="M0 60 H450 C490 60 520 22 600 20 C680 22 700 60 740 60 H1200 V60Z" fill="#fff"/>
  </svg>
</section>

<h2 class="section-title" style="top:3146px">Pricing and Packages</h2>
<div class="pricing">
  <div class="photo" style="position:relative" role="img" aria-label="Truck wheel being sprayed with water" style=""></div>
  <div class="price-panel">
    <h3>Individual Pricing</h3>
    <p>Lorem ipsum dolor sit amet, consectetur adipiscing elit, sed do eiusmod tempor inci didunt ut labore et dolore magna aliqua.</p>
    <a class="btn btn-white">Learn More</a>
  </div>
  <div class="photo" style="position:relative;background:linear-gradient(180deg,#6f7c88,#2e3640 60%,#8a8f4a)" role="img" aria-label="Fleet truck exiting the wash bay"></div>
  <div class="price-panel">
    <h3>Fleet Packages</h3>
    <p>Lorem ipsum dolor sit amet, consectetur adipiscing elit, sed do eiusmod tempor inci didunt ut labore et dolore magna aliqua.</p>
    <a class="btn btn-white">Learn More</a>
  </div>
</div>
<style>.pricing > div:first-child{background:linear-gradient(135deg,#d8dde2,#6f7780 55%,#2f3338)}</style>

<footer class="site-footer">
  <div class="footer-logo">Brightlane<br>Rapid Rinse</div>
  <div class="footer-divider-v"></div>
  <div class="news">
    <h4>News Subscription</h4>
    <p>Get Latest Deals from Brightlane's Inbox &amp;<br>Subscribe Now</p>
  </div>
  <div class="email-field"><span>Email Address</span><svg width="14" height="12" viewBox="0 0 14 12"><rect x="1" y="1.5" width="12" height="9" fill="none" stroke="#7BADD7" stroke-width="1.3"/><path d="M1 2l6 5 6-5" fill="none" stroke="#7BADD7" stroke-width="1.3"/></svg></div>
  <div class="subscribe">Subscribe</div>
  <div class="footer-rule"></div>

  <div class="footer-col"><h5 style="left:112px">About Company</h5></div>
  <p class="footer-about">Lorem ipsum dolor sit amet, consectetur adipiscing elit, sed do labore et dolore magna aliqua.</p>
  <div class="socials"><span></span><span></span><span></span><span></span><span></span></div>

  <div class="footer-col"><h5 style="left:423px">Quick Links</h5></div>
  <ul class="footer-list" style="left:423px"><li>Home page</li><li>About us</li><li>Why Brightlane</li><li>Services and pricing</li></ul>
  <ul class="footer-list" style="left:654px"><li>Videos of wash system</li><li>Fleets</li><li>contact us</li></ul>

  <div class="footer-col"><h5 style="left:903px">Services</h5></div>
  <ul class="footer-list" style="left:903px"><li>Automated Truck Wash</li><li>Additional Services</li><li>Fleet Services</li></ul>
</footer>
<div class="copyright">Copyright © 2024 Brightlane Rapid Rinse. All rights reserved. Privacy Policy</div>

</body>
</html>
```